Web Design for a Biotech Consulting Firm

We need a web site design for a new business based in Philadelphia called Verantel Dx. This is a consulting firm that will serve medical diagnostics industry, which is part of the life science/healthcare industry focusing on developing and marketing products that help in early detection, monitoring or management of diseases. Our consulting firm will help medical diagnostic companies to overcome key challenges in designing, evaluating and marketing new products.Our company name is Verantel Dx. Verantel is Latin word for "something" Dx represents diagnostics. The idea behind the name is that we help companies to transform the original, early product ideas ("nothing") into "something"; which is a product with full clinical utility that will help to improve health and well-being.The web site should use the visual feel of the logo (attached), be modern, simple and clean looking and represent creativity, innovation, scientific thinking and progress.
Updates

Wix Design is acceptable

Industry/Entity Type

Biotechnology

Coding

Coded - Design and coding required

Number of Pages Required

1 page

Font styles to use
Sans Serif

Requirements
Must have
• simple, clean look couple of pages
Should not have
• a lot of pages

```html
<!DOCTYPE html>
<html lang="en">
<head>
<meta charset="utf-8">
<title>Verantel Dx — Biotech Consulting</title>
<link rel="stylesheet" href="https://fonts.googleapis.com/css2?family=Mulish:wght@300;400;600;700&family=Nunito+Sans:wght@400;600;700&display=swap">
<style>
:root{
  --blue:#3d7bd0;
  --blue-dark:#0f3f7e;
  --blue-band:#4a86d6;
  --ink:#1d1d1f;
  --muted:#555a63;
  --line:#c9d3e0;
  --pale:#eef3fa;
  --panel:#f5f6f8;
  --white:#ffffff;
}
*{box-sizing:border-box;margin:0;padding:0}
html,body{width:1200px;height:3457px;overflow:hidden;background:var(--white);font-family:"Mulish",sans-serif;color:var(--ink)}
.page{position:relative;width:1200px;height:3457px}
.abs{position:absolute}
.brand{font-family:"Nunito Sans",sans-serif;font-weight:600;color:var(--ink);display:flex;align-items:center;gap:8px}
.brand-mark{width:10px;height:10px;background:var(--blue)}
.btn{position:absolute;display:flex;align-items:center;justify-content:center;border:1.5px solid var(--blue);font-size:15px;color:var(--ink);background:transparent}
.btn::after{content:"";position:absolute;right:-14px;top:50%;width:16px;height:1px;background:var(--blue)}
.btn.light{border-color:var(--white);color:var(--white)}
.btn.light::after{background:var(--white)}

/* header */
.site-header{position:absolute;left:0;top:0;width:1200px;height:100px;border-bottom:1px solid #e6e9ee}
.site-header .brand{position:absolute;left:141px;top:34px;font-size:19px}
.nav{position:absolute;top:38px;font-size:15px;color:var(--muted)}
.nav.active{color:var(--ink);font-weight:700;border:1px solid var(--blue);padding:3px 7px;top:34px}
.header-phone{position:absolute;left:935px;top:28px;display:flex;gap:10px;align-items:center;border-left:1px solid #dde2ea;padding-left:14px}
.header-phone small{display:block;font-size:13px;color:var(--muted);letter-spacing:.5px}
.header-phone span{font-size:13px;color:var(--ink)}

/* hero */
.hero{position:absolute;left:0;top:100px;width:1200px;height:542px;background:linear-gradient(100deg,#2b6ab9 0%,#1a4f98 35%,#0f3f7e 70%,#0b3570 100%)}
.hero-art{position:absolute;left:0;top:0;width:560px;height:542px;background:radial-gradient(ellipse at 60% 35%,#9bd94a 0%,#4b9a62 18%,#2a64ad 45%,transparent 75%)}
.hero h1{position:absolute;left:639px;top:180px;font-family:"Nunito Sans",sans-serif;font-weight:600;font-size:33px;line-height:47px;color:var(--white);letter-spacing:.5px}
.dots{position:absolute;left:633px;top:485px;display:flex;gap:12px}
.dots i{width:14px;height:14px;border:1.5px solid var(--white)}
.dots i.on{background:var(--white)}

/* challenges */
.challenges h2{position:absolute;left:0;width:1200px;top:727px;text-align:center;font-family:"Nunito Sans",sans-serif;font-weight:600;font-size:29px}
.challenges h3{position:absolute;left:0;width:1200px;top:770px;text-align:center;font-weight:400;font-size:29px;color:var(--blue)}
.step-num{position:absolute;top:885px;font-family:"Nunito Sans",sans-serif;font-size:120px;line-height:120px;font-weight:300;color:transparent;-webkit-text-stroke:1.5px #c8ccd2}
.step-num.on{-webkit-text-stroke-color:var(--blue)}
.card{position:absolute;top:856px;height:206px;border:1.5px solid #c8ccd2;background:var(--white);text-align:center}
.card.on{border-color:var(--blue)}
.card svg{margin-top:22px}
.card h4{font-weight:400;font-size:19px;margin-top:10px}
.card p{font-size:12.5px;color:var(--muted);line-height:16px;margin:12px auto 0;width:170px}

/* about */
.about{position:absolute;left:0;top:1232px;width:1200px;height:439px;background:radial-gradient(ellipse at 80% 40%,#7aa8e6 0%,#4f88d7 40%,#3c78cf 100%);color:var(--white);text-align:center}
.about-art{position:absolute;left:0;top:0;width:1200px;height:439px}
.about h2{position:absolute;left:0;width:1200px;top:88px;font-family:"Nunito Sans",sans-serif;font-weight:600;font-size:29px}
.about .rule{position:absolute;left:564px;top:140px;width:72px;height:1px;background:rgba(255,255,255,.8)}
.about .lead{position:absolute;left:0;width:1200px;top:162px;font-size:15px;line-height:23px}
.about .body{position:absolute;left:170px;width:860px;top:222px;font-size:13.5px;line-height:21.5px}

/* asset */
.asset-photo{position:absolute;left:0;top:1671px;width:648px;height:435px;background:linear-gradient(120deg,#dce8f2 0%,#b8d3ea 45%,#eaf1f7 100%)}
.asset h2{position:absolute;left:722px;top:1830px;font-family:"Nunito Sans",sans-serif;font-weight:600;font-size:29px}
.asset h2 em,.news h2 em,.contact h2 em{font-style:normal;color:var(--blue)}
.asset p{position:absolute;left:720px;top:1878px;font-size:19px;line-height:29px;color:#333}

/* stats */
.stats{position:absolute;left:0;top:2106px;width:1200px;height:220px;background:var(--pale)}
.stat{position:absolute;top:75px;width:240px;text-align:center}
.stat b{display:block;font-size:36px;font-weight:600;color:var(--blue);line-height:40px}
.stat span{display:block;font-size:15px;margin-top:6px;letter-spacing:.3px}
.stat-div{position:absolute;top:70px;width:0;height:84px;border-left:1px dashed #9fb6d6}

/* news */
.news{position:absolute;left:0;top:2326px;width:1200px;height:439px;background:linear-gradient(90deg,#f3f5f8 0%,#eceff3 45%,#d6dde6 65%,#c9d3de 100%)}
.news-photo{position:absolute;left:560px;top:0;width:640px;height:439px;background:linear-gradient(100deg,rgba(220,228,236,0) 0%,#c3ccd6 30%,#aab6c2 60%,#d9dfe6 100%)}
.news h2{position:absolute;left:141px;top:86px;font-family:"Nunito Sans",sans-serif;font-weight:600;font-size:28px}
.item{position:absolute;left:143px;width:350px}
.item p{font-size:13.5px;line-height:21px;color:#333}
.item .meta{display:flex;justify-content:space-between;align-items:center;margin-top:12px;font-size:13.5px;width:340px}
.item .meta span{display:flex;gap:8px;align-items:center}
.item .meta b{font-size:12.5px;font-weight:700;letter-spacing:.3px;position:relative;padding-right:26px}
.item .meta b::after{content:"";position:absolute;right:0;top:7px;width:16px;height:1px;background:#777}
.news .sep{position:absolute;left:141px;top:251px;width:352px;border-top:1px dashed #9fb6d6}

/* contact */
.contact h2{position:absolute;left:0;width:1200px;top:2848px;text-align:center;font-family:"Nunito Sans",sans-serif;font-weight:600;font-size:29px;letter-spacing:.5px}
.contact-box{position:absolute;left:141px;top:2928px;width:917px;height:326px;background:var(--panel)}
.contact-info{position:absolute;left:599px;top:0;width:318px;height:326px;background:var(--pale)}
.field{position:absolute;font-size:12.5px;color:#444;border-bottom:1px dashed #9fb6d6;padding-bottom:14px}
.info{position:absolute;left:36px;display:flex;gap:20px;font-size:13.5px;line-height:21px;color:#222}
.info i{width:40px;height:40px;border:1.5px solid var(--blue);display:flex;align-items:center;justify-content:center;flex:none;background:var(--white)}

/* footer */
.site-footer .brand{position:absolute;left:191px;top:3350px;font-size:19px}
.foot-nav{position:absolute;top:3355px;font-size:13px;color:#333}
.foot-dot{position:absolute;top:3363px;width:4px;height:4px;border-radius:50%;background:#bbb}
.copy{position:absolute;right:142px;top:3356px;font-size:13px;color:#333}
.bottom-bar{position:absolute;left:0;top:3454px;width:1200px;height:3px;background:var(--blue)}
</style>
</head>
<body>
<div class="page">

<header class="site-header">
  <div class="brand"><span class="brand-mark"></span>Verantel Dx</div>
  <a class="nav active" style="left:530px">Home</a>
  <a class="nav" style="left:619px">About Us</a>
  <a class="nav" style="left:723px">Services</a>
  <a class="nav" style="left:821px">Contact Us</a>
  <div class="header-phone">
    <svg width="26" height="26" viewBox="0 0 26 26"><circle cx="13" cy="13" r="12" fill="none" stroke="#3d7bd0" stroke-width="1.5"/><path d="M9 8c1-1 2 0 2.5 1.5S11 11 11 12c.8 1.6 1.8 2.6 3 3 1 0 1.5-1 2.5-.5S18 16 17 17c-3 1.5-9-5-8-9z" fill="#3d7bd0"/></svg>
    <div><small>PHONE</small><span>123-456-7890</span></div>
  </div>
</header>

<section class="hero">
  <div class="hero-art" role="img" aria-label="Gloved hand holding a glowing test tube with a leaf in front of a blue DNA helix and molecular diagram"></div>
  <h1>We Are<br>A Biotech Consulting Firm<br>Serving The Medical<br>Diagnostics Industry</h1>
  <div class="dots"><i class="on"></i><i></i><i></i><i></i></div>
</section>

<section class="challenges">
  <h2>Our Consulting Firm Will Help Medical Diagnostic Companies</h2>
  <h3>To Overcome Key Challenges In</h3>

  <div class="step-num" style="left:138px">1</div>
  <div class="card" style="left:197px;width:225px">
    <svg width="56" height="54" viewBox="0 0 56 54" fill="none" stroke="#888" stroke-width="1.5"><circle cx="28" cy="27" r="14"/><circle cx="14" cy="14" r="4"/><circle cx="28" cy="6" r="4"/><circle cx="14" cy="40" r="4"/><circle cx="42" cy="40" r="4"/><path d="M40 6c8 0 12 6 10 14-6 0-10-6-10-14z"/></svg>
    <h4>Designing</h4>
    <p>Lorem ipsum dolor sit amet, consectetuer adipiscing sed diam nonummy</p>
  </div>

  <div class="step-num on" style="left:455px">2</div>
  <div class="card on" style="left:525px;width:216px">
    <svg width="58" height="58" viewBox="0 0 58 58" fill="none" stroke="#3d7bd0" stroke-width="1.5"><rect x="6" y="22" width="46" height="28"/><path d="M2 50h54v4H2z"/><circle cx="29" cy="16" r="12"/><path d="M29 10v6h5"/><path d="M12 44v-6M18 44v-10M24 44v-8M34 44v-12M40 44v-6M46 44v-9"/></svg>
    <h4>Market Analysis</h4>
    <p>Lorem ipsum dolor sit amet, consectetuer adipiscing sed diam nonummy</p>
  </div>

  <div class="step-num" style="left:778px">3</div>
  <div class="card" style="left:847px;width:211px">
    <svg width="74" height="56" viewBox="0 0 74 56" fill="none" stroke="#888" stroke-width="1.5"><rect x="4" y="6" width="44" height="30"/><path d="M20 44h12M26 36v8"/><rect x="10" y="12" width="14" height="10"/><path d="M48 18l14-8v28l-14-8z"/><path d="M66 16l5-3M66 24h6M66 32l5 3"/></svg>
    <h4>Product Launch</h4>
    <p>Lorem ipsum dolor sit amet, consectetuer adipiscing sed diam nonummy</p>
  </div>

  <a class="btn" style="left:548px;top:1106px;width:98px;height:34px">Get Started</a>
</section>

<section class="about">
  <div class="about-art" role="img" aria-label="Soft blue background with DNA helix, hexagon pattern and a close-up of an eye"></div>
  <h2>About Verantel Dx</h2>
  <div class="rule"></div>
  <p class="lead">Verantel Dx This Is A Consulting Firm That Will Serve Medical Diagnostics Industry,<br>Which Is Part of The Life Science/healthcare Industry</p>
  <p class="body">Lorem ipsum dolor sit amet, consectetuer adipiscing elit, sed diam nonummy nibh euismod tincidunt ut laoreet dolore magna aliquam erat volutpat. Ut wisi enim ad minim veniam, quis nostrud exerci tation ullamcorper suscipit lobortis nisl ut aliquip ea commodo consequat. Duis autem vel eum iriure or sit amet, consectetuer adipiscing elit</p>
  <a class="btn light" style="left:543px;top:311px;width:105px;height:34px">Read More</a>
</section>

<section class="asset">
  <div class="asset-photo" role="img" aria-label="Scientist in safety glasses working with glassware next to a microscope in a bright lab"></div>
  <h2>Asset <em>Partnering</em></h2>
  <p>Learn about our current partnering<br>opportunities and submit your assets.</p>
  <a class="btn" style="left:719px;top:1958px;width:96px;height:34px">Learn More</a>
</section>

<section class="stats">
  <div class="stat" style="left:112px"><b>100</b><span>PROFESSIONAL STAFF</span></div>
  <div class="stat-div" style="left:381px"></div>
  <div class="stat" style="left:350px"><b>50</b><span>ROOMS</span></div>
  <div class="stat-div" style="left:560px"></div>
  <div class="stat" style="left:566px"><b>10</b><span>STARS COMFORT</span></div>
  <div class="stat-div" style="left:813px"></div>
  <div class="stat" style="left:844px"><b>25</b><span>YEARS OF EXPERIENCE</span></div>
</section>

<section class="news">
  <div class="news-photo" role="img" aria-label="Smiling lab researchers working at microscopes"></div>
  <h2>Latest <em>News</em></h2>
  <div class="item" style="top:146px">
    <p>Lorem Quis nostrud exerci tation ullamcorper suscipit lobortis nisl ut aliquip ex ea commo</p>
    <div class="meta"><span><svg width="14" height="14" viewBox="0 0 14 14" fill="none" stroke="#3d7bd0" stroke-width="1.3"><rect x="1" y="2" width="12" height="11"/><path d="M1 5h12M4 0v3M10 0v3"/></svg>June 17, 2019</span><b>READ MORE</b></div>
  </div>
  <div class="sep"></div>
  <div class="item" style="top:281px">
    <p>Lorem Quis nostrud exerci tation ullamcorper suscipit lobortis nisl ut aliquip ex ea commo</p>
    <div class="meta"><span><svg width="14" height="14" viewBox="0 0 14 14" fill="none" stroke="#3d7bd0" stroke-width="1.3"><rect x="1" y="2" width="12" height="11"/><path d="M1 5h12M4 0v3M10 0v3"/></svg>June 17, 2019</span><b>READ MORE</b></div>
  </div>
</section>

<section class="contact">
  <h2>CONTACT <em>US</em></h2>
  <div class="contact-box">
    <div class="field" style="left:36px;top:60px;width:235px">Name</div>
    <div class="field" style="left:301px;top:60px;width:234px">Phone</div>
    <div class="field" style="left:36px;top:114px;width:235px">Email</div>
    <div class="field" style="left:301px;top:114px;width:234px">Company Name</div>
    <div class="field" style="left:36px;top:168px;width:499px;padding-bottom:32px">Message</div>
    <a class="btn" style="left:37px;top:235px;width:96px;height:35px">SUBMIT</a>

    <div class="contact-info">
      <div class="info" style="top:60px"><i><svg width="14" height="18" viewBox="0 0 14 18"><path d="M7 0a7 7 0 0 1 7 7c0 5-7 11-7 11S0 12 0 7a7 7 0 0 1 7-7z" fill="#3d7bd0"/><circle cx="7" cy="7" r="2.5" fill="#fff"/></svg></i><div>Lorem Quis nostrud exercitionl<br>ullamcorper suscipit - 123 456</div></div>
      <div class="info" style="top:138px"><i><svg width="18" height="18" viewBox="0 0 18 18"><path d="M3 2c2-1 3 1 3.5 3S5 7 5 8c1 2 3 4 5 5 1 0 2-2 3.5-1.5S17 13 16 15c-5 3-16-8-13-13z" fill="#3d7bd0"/></svg></i><div>CALL US :<br>123-456-7890</div></div>
      <div class="info" style="top:216px"><i><svg width="18" height="18" viewBox="0 0 18 18"><path d="M17 1L1 8l6 2 2 7 8-16z" fill="#3d7bd0"/><path d="M7 10l10-9" stroke="#fff" stroke-width="1"/></svg></i><div>EMAIL US:<br>info@veranteldx.com</div></div>
    </div>
  </div>
</section>

<footer class="site-footer">
  <div class="brand"><span class="brand-mark"></span>Verantel Dx</div>
  <a class="foot-nav" style="left:352px">Home</a>
  <span class="foot-dot" style="left:404px"></span>
  <a class="foot-nav" style="left:427px">About Us</a>
  <span class="foot-dot" style="left:496px"></span>
  <a class="foot-nav" style="left:519px">Services</a>
  <span class="foot-dot" style="left:586px"></span>
  <a class="foot-nav" style="left:611px">Contact Us</a>
  <p class="copy">Copyright © 2019 Verantel Dx . All Rights Reserved.</p>
  <div class="bottom-bar"></div>
</footer>

</div>
</body>
</html>
```